Need help in designing new business card utilizing our new logo.

BuildMark Solutions works with Construction Business Owners, Managers & IT Professionals to strengthen software usage and increase user productivity.

Our Construction Accounting and Mobile Field Management Software Clients engage with us in the following areas:

New Software Implementations
Software Re-Implementations
Redesigning Software Usage at the User Level
Project Coordination & Management
Continued Software Support

Old tag line:
Weighing Options - Implementing Solutions

www.buildmark-solutions.example

Ridge 4 is a product, but not needed for a new business card.

```html
<!DOCTYPE html>
<html lang="en">
<head>
<meta charset="utf-8">
<title>BuildMark Solutions – Business Card</title>
<link href="https://fonts.googleapis.com/css2?family=Open+Sans:wght@400;600;700&display=swap" rel="stylesheet">
<style>
  :root {
    --backdrop: #2e2e2e;
    --brand-blue: #0d17a8;
    --card-white: #ffffff;
    --edge-grey: #c4c4c4;
    --name-grey: #c8c8cc;
    --text-white: #ffffff;
    --text-grey: #555555;
  }
  * { margin: 0; padding: 0; box-sizing: border-box; }
  html, body { width: 1200px; height: 960px; overflow: hidden; }
  body {
    background: var(--backdrop);
    font-family: "Open Sans", Arial, sans-serif;
    position: relative;
  }
  .card {
    position: absolute;
    width: 600px;
    height: 342px;
    box-shadow: 0 2px 6px rgba(0,0,0,0.45);
  }
  /* Front */
  .card-front { left: 322px; top: 110px; background: var(--card-white); }
  .front-panel {
    position: absolute; left: 0; top: 0; width: 269px; height: 100%;
    background: var(--brand-blue); color: var(--text-white);
  }
  .front-edge {
    position: absolute; right: 0; top: 0; width: 18px; height: 100%;
    background: var(--edge-grey);
  }
  .holder-name {
    position: absolute; left: 22px; top: 78px;
    font-weight: 700; font-size: 19px; letter-spacing: -0.2px;
    color: var(--name-grey);
  }
  .holder-title {
    position: absolute; left: 22px; top: 102px;
    font-weight: 700; font-size: 15px; color: var(--name-grey);
  }
  .holder-address {
    position: absolute; left: 22px; top: 130px;
    font-size: 14px; line-height: 20px;
  }
  .holder-contact {
    position: absolute; left: 24px; top: 181px;
    font-size: 14px; line-height: 19px; list-style: none;
  }
  .brand-lockup {
    position: absolute; left: 269px; width: 313px; top: 130px;
    display: flex; align-items: center; justify-content: center; gap: 10px;
  }
  .brand-mark {
    width: 16px; height: 16px; background: var(--brand-blue);
  }
  .brand-name {
    font-weight: 600; font-size: 22px; color: var(--brand-blue);
  }
  .brand-descriptor {
    position: absolute; left: 269px; width: 313px; top: 195px;
    text-align: center; font-size: 14px; line-height: 19px;
    color: var(--text-grey); text-transform: uppercase;
  }
  /* Back */
  .card-back { left: 320px; top: 493px; background: var(--brand-blue); color: var(--text-white); }
  .back-brand {
    position: absolute; left: 40px; top: 135px; width: 180px;
    display: flex; align-items: center; gap: 10px;
  }
  .back-brand .brand-mark { background: var(--text-white); width: 20px; height: 20px; }
  .back-brand .brand-name { color: var(--text-white); font-size: 20px; line-height: 26px; }
  .service-intro {
    position: absolute; left: 236px; top: 77px;
    font-weight: 600; font-size: 14px; line-height: 19px; text-transform: uppercase;
  }
  .service-list {
    position: absolute; left: 234px; top: 155px;
    list-style: none; font-size: 14px; line-height: 19px;
  }
  .service-list li::before { content: "• "; }
  .tagline {
    position: absolute; left: 107px; top: 296px;
    font-size: 14px; text-transform: uppercase;
  }
</style>
</head>
<body>
  <section class="card card-front">
    <div class="front-panel">
      <p class="holder-name">DANA R. WHITFIELD</p>
      <p class="holder-title">OWNER</p>
      <p class="holder-address">48 harbor lane-Suite 12<br>millbrook NY 12545</p>
      <ul class="holder-contact">
        <li>P. 800-555-0142ext.100</li>
        <li>M. 518-555-0193</li>
        <li>dana.whitfield@buildmark-solutions.example</li>
        <li>www.buildmark-solutions.example</li>
      </ul>
    </div>
    <div class="brand-lockup">
      <span class="brand-mark"></span>
      <span class="brand-name">BuildMark Solutions</span>
    </div>
    <p class="brand-descriptor">Construction Accounting<br>Software Consultants</p>
    <div class="front-edge"></div>
  </section>

  <section class="card card-back">
    <div class="back-brand">
      <span class="brand-mark"></span>
      <span class="brand-name">BuildMark Solutions</span>
    </div>
    <p class="service-intro">Our construction accounting<br>and mobile field management<br>software clients engage with us<br>in the following areas:</p>
    <ul class="service-list">
      <li>New Software Implementations</li>
      <li>Software Re-Implementations</li>
      <li>Redesigning Software Usage at the User Level</li>
      <li>Project Coordination &amp; Management</li>
      <li>Continued Software Support</li>
    </ul>
    <p class="tagline">Weighing Options - Implementing Solutions</p>
  </section>
</body>
</html>
```